Cat-products company needs smart, yet endearing, business card

We need a business card design for a new, but up-and-running, business based in Honolulu, Hawaii. The business is Purrnest Nook Co. Our first product is the most environmentally-friendly cat grass kit ever seen on the planet. Future products, currently in the R&D phase, will include a variety of exciting cat scratchers. We also do consulting work to help apartment-dwellers make their home more cat-friendly and, in the future, plan on doing full, custom installs of structure to create high walkways for cats.

Target Market(s)

Middle-aged, apartment-dwelling, middle-class workers who own 1 or more cats and who dote on them.

Industry/Entity Type

Pet Care

Contact Information for Business Card

A striking, professional, yet warm and friendly design is what we're after.

Font styles to use
Serif
Sans Serif
Other font styles liked:
• Comfortaa

Colors

Designer to choose colors to be used in the design.

Requirements
Must have
• The company logo: (see attachment)
• The company name: Purrnest Nook Co
• The web address: www.purrnestnookco.com
• Email: support@purrnestnookco.com
• Phone: +1 (808) 571 6023
• Update (Fri Jun 30 3017 7:45pm Hawaii Time) I would like, is possible, uploaded picture of the cat grass kit on the back of the card with some text along the lines of: Purrnest Nook Co - Maker Of The Leafiest Feline Sprout Set Yet
Nice to have
• A cat picture, cartoon, real or silhouette that illustrates cats in action and/or relaxing; ie using the apartment space to live, play and relax in and being well-contented.
• Most of the website is done in the font: Comfortaa. It might be nice to continue using this for brand consistency.
Should not have
• Hard-to-read fonts.

```html
<!DOCTYPE html>
<html lang="en">
<head>
<meta charset="utf-8">
<title>Purrnest Nook Co – Business Card</title>
<link rel="stylesheet" href="https://fonts.googleapis.com/css2?family=PT+Sans+Narrow:wght@700&family=Questrial&display=swap">
<style>
  :root {
    --backdrop: #2b2b2b;
    --card-white: #f3f3f3;
    --brown: #53322b;
    --gold: #f0a90a;
    --ink: #4a4a4a;
    --rule: #bdbdbd;
    --social: #8a6a60;
  }
  * { box-sizing: border-box; margin: 0; padding: 0; }
  html, body { width: 1200px; height: 960px; overflow: hidden; }
  body {
    background: var(--backdrop);
    position: relative;
    font-family: "Questrial", sans-serif;
  }
  .card {
    position: absolute;
    width: 600px;
    height: 343px;
    border-radius: 20px;
    overflow: hidden;
  }
  .card--front { left: 314px; top: 113px; background: var(--card-white); }
  .card--back { left: 311px; top: 472px; background: var(--brown); }

  /* Front */
  .brand {
    position: absolute;
    left: 40px; top: 120px;
    width: 240px;
    display: flex; align-items: center; justify-content: center; gap: 10px;
  }
  .brand__square { width: 22px; height: 22px; background: var(--gold); flex: none; }
  .brand__name {
    font-size: 27px;
    line-height: 1.1;
    color: var(--brown);
  }
  .divider {
    position: absolute;
    left: 283px; top: 86px;
    width: 1px; height: 170px;
    background: linear-gradient(to bottom, transparent, var(--rule) 20%, var(--rule) 80%, transparent);
  }
  .contact { position: absolute; left: 322px; top: 90px; }
  .contact__name {
    font-family: "PT Sans Narrow", sans-serif;
    font-weight: 700;
    font-size: 25px;
    color: var(--brown);
    line-height: 1;
  }
  .contact__role {
    font-size: 15px;
    color: var(--gold);
    margin-top: 4px;
  }
  .contact__address {
    font-size: 15px;
    color: var(--ink);
    line-height: 19px;
    margin-top: 14px;
  }
  .contact__lines { margin-top: 11px; font-size: 15px; color: var(--ink); line-height: 19px; }
  .contact__line { display: flex; align-items: center; gap: 8px; }
  .contact__line svg { width: 13px; height: 13px; fill: var(--brown); flex: none; }
  .stripe {
    position: absolute; left: 0; bottom: 0;
    width: 360px; height: 11px;
    background: var(--gold);
  }
  .web-tab {
    position: absolute; right: 0; bottom: 0;
    width: 252px; height: 35px;
    background: var(--brown);
    clip-path: polygon(34px 0, 100% 0, 100% 100%, 0 100%);
    display: flex; align-items: center; justify-content: flex-end;
    padding-right: 18px;
    color: #fff; font-size: 15px;
  }

  /* Back */
  .social { position: absolute; right: 18px; top: 19px; display: flex; gap: 2px; }
  .social__dot { width: 22px; height: 22px; border-radius: 50%; background: var(--social); }
  .back-brand {
    position: absolute; left: 0; right: 0; top: 120px;
    display: flex; align-items: center; justify-content: center; gap: 14px;
  }
  .back-brand__circle { width: 40px; height: 40px; border-radius: 50%; background: var(--gold); }
  .back-brand__name { font-size: 44px; color: var(--gold); }
  .back-web {
    position: absolute; left: 0; right: 0; top: 294px;
    text-align: center;
    color: #fff; font-size: 15px; letter-spacing: 4px;
  }
</style>
</head>
<body>
  <section class="card card--front">
    <div class="brand">
      <span class="brand__square"></span>
      <span class="brand__name">Purrnest Nook Co</span>
    </div>
    <div class="divider"></div>
    <div class="contact">
      <p class="contact__name">MAYA KEALOHA</p>
      <p class="contact__role">CEO/FOUNDER</p>
      <p class="contact__address">2216 Plumeria Lane<br>Honolulu, Hawaii 96814</p>
      <div class="contact__lines">
        <p class="contact__line">
          <svg viewBox="0 0 24 24" aria-hidden="true"><path d="M6.6 10.8a15.1 15.1 0 0 0 6.6 6.6l2.2-2.2a1 1 0 0 1 1-.25 11.4 11.4 0 0 0 3.6.57 1 1 0 0 1 1 1V20a1 1 0 0 1-1 1A17 17 0 0 1 3 4a1 1 0 0 1 1-1h3.5a1 1 0 0 1 1 1c0 1.25.2 2.45.57 3.57a1 1 0 0 1-.25 1z"/></svg>
          +1 (808) 571 6023
        </p>
        <p class="contact__line">
          <svg viewBox="0 0 24 24" aria-hidden="true"><path d="M2 5h20v14H2z" fill="none"/><path d="M2 5h20v2l-10 6L2 7zM2 9l10 6 10-6v10H2z"/></svg>
          support@purrnestnookco.com
        </p>
      </div>
    </div>
    <div class="stripe"></div>
    <div class="web-tab">www.purrnestnookco.com</div>
  </section>

  <section class="card card--back">
    <div class="social">
      <span class="social__dot"></span>
      <span class="social__dot"></span>
      <span class="social__dot"></span>
      <span class="social__dot"></span>
    </div>
    <div class="back-brand">
      <span class="back-brand__circle"></span>
      <span class="back-brand__name">Purrnest Nook Co</span>
    </div>
    <p class="back-web">www.purrnestnookco.com</p>
  </section>
</body>
</html>
```